Looking for a cool & simple business-card-design for digital agency

Hi!

We are a web agency that offers Reputation Management, Vextor & Seo Services and software development. We like cool things, we like innovative styles.

We have uploaded our logo.

Project Deadline Extended Reason: Client does not want any designs with the colorful logo. Please send us submissions ONLY with the blac and white logo. What the client would like to see:1) Back of the card: is a silver logo on a black background2) front of the card with all the data, please use white background and black logo thank you Added Friday, May 8, 2015

Industry/Entity Type

Software

```html
<!DOCTYPE html>
<html lang="de">
<head>
<meta charset="utf-8">
<title>Kelvra AG – Business Card</title>
<link rel="stylesheet" href="https://fonts.googleapis.com/css2?family=Lato:wght@400;700;900&display=swap">
<style>
  :root {
    --stage: #e9e7e3;
    --card-black: #050505;
    --card-white: #ffffff;
    --ink: #111111;
    --silver: #c9c9c9;
    --rule: #1a1a1a;
    --shadow: rgba(0, 0, 0, 0.28);
  }
  * { box-sizing: border-box; margin: 0; padding: 0; }
  html, body {
    width: 1200px;
    height: 900px;
    overflow: hidden;
    background: var(--stage);
    font-family: "Lato", "Helvetica Neue", Arial, sans-serif;
  }
  .stage {
    width: 1200px;
    height: 900px;
    display: flex;
    flex-direction: column;
    align-items: center;
    justify-content: center;
    gap: 44px;
  }
  .card {
    position: relative;
    width: 680px;
    height: 388px;
    box-shadow: 0 14px 30px var(--shadow);
  }

  /* Back */
  .card--back {
    background: var(--card-black);
    display: flex;
    align-items: center;
    justify-content: center;
  }
  .card--back .brand-name {
    color: var(--silver);
    font-size: 64px;
    font-weight: 900;
    letter-spacing: 1px;
  }
  .brand {
    display: flex;
    align-items: center;
    gap: 16px;
  }
  .brand-square {
    width: 34px;
    height: 34px;
  }
  .card--back .brand-square { background: var(--silver); }

  /* Front */
  .card--front {
    background: var(--card-white);
    color: var(--ink);
  }
  .card--front .brand {
    position: absolute;
    left: 46px;
    top: 42px;
  }
  .card--front .brand-square { background: var(--ink); width: 30px; height: 30px; }
  .card--front .brand-name {
    font-size: 48px;
    font-weight: 900;
    letter-spacing: 0.5px;
  }
  .top-rule {
    position: absolute;
    left: 46px;
    right: 46px;
    top: 134px;
    height: 2px;
    background: var(--rule);
  }
  .contact-list {
    position: absolute;
    left: 46px;
    top: 152px;
    list-style: none;
    font-size: 19px;
    line-height: 27px;
  }
  .contact-list li {
    display: flex;
    align-items: center;
    gap: 8px;
  }
  .contact-list svg {
    width: 15px;
    height: 15px;
    flex: none;
  }
  .person {
    position: absolute;
    right: 46px;
    bottom: 46px;
    text-align: right;
  }
  .person-name {
    font-size: 21px;
    font-weight: 900;
  }
  .person-role {
    font-size: 19px;
    font-weight: 400;
    margin-top: 2px;
  }
  .bottom-rule {
    position: absolute;
    left: 400px;
    right: 46px;
    bottom: 34px;
    height: 2px;
    background: var(--rule);
  }
</style>
</head>
<body>
<main class="stage">

  <section class="card card--back" aria-label="Card back">
    <div class="brand">
      <span class="brand-square"></span>
      <span class="brand-name">Kelvra AG</span>
    </div>
  </section>

  <section class="card card--front" aria-label="Card front">
    <div class="brand">
      <span class="brand-square"></span>
      <span class="brand-name">Kelvra AG</span>
    </div>
    <div class="top-rule"></div>

    <ul class="contact-list">
      <li>
        <svg viewBox="0 0 16 16" aria-hidden="true"><path d="M2 6c0-2 2-3 6-3s6 1 6 3l-3 1-1-2H6L5 7 2 6z M4 8h8l1 5H3z" fill="#111"/></svg>
        041 555 0182
      </li>
      <li>
        <svg viewBox="0 0 16 16" aria-hidden="true"><rect x="4" y="1" width="8" height="14" rx="1.5" fill="none" stroke="#111" stroke-width="1.6"/><circle cx="8" cy="12.5" r="0.9" fill="#111"/></svg>
        079 555 3046
      </li>
      <li>
        <svg viewBox="0 0 16 16" aria-hidden="true"><rect x="1" y="3" width="14" height="10" fill="none" stroke="#111" stroke-width="1.5"/><path d="M1 3l7 6 7-6" fill="none" stroke="#111" stroke-width="1.5"/></svg>
        info@kelvra-ag.com
      </li>
      <li>
        <svg viewBox="0 0 16 16" aria-hidden="true"><circle cx="8" cy="8" r="6.5" fill="#111"/><path d="M1.5 8h13M8 1.5c-3 3-3 10 0 13M8 1.5c3 3 3 10 0 13M2.8 4.8h10.4M2.8 11.2h10.4" fill="none" stroke="#fff" stroke-width="0.9"/></svg>
        www.kelvra-ag.com
      </li>
    </ul>

    <div class="person">
      <p class="person-name">Mara Lenz</p>
      <p class="person-role">Director</p>
    </div>
    <div class="bottom-rule"></div>
  </section>

</main>
</body>
</html>
```